Modern Medical Optometry Website

We need mordern, Patient friendly website. Easy to navigate and enhance our advance medical technology and excellent patient care.
1. HOME PAGE
2. OUR TEAM PAGE
3. EYECARE PAGE - VISION SERVICES, EYE EXAMS, KERATOCONUS CENTER, GLAUCOMA , DIABITES, MELORIDEX EXAM, DIGITAL RETINAL, OCT.
4. MYOPIA CONTROL CLINIC
5. DRY EYE CLINIC
6. EYEWEAR
7. PATIENT CENTER - BLOG
7. CONTACT US
This is our current website www.brivaloka.com
and We want to add more content and a cleaner design like these website
http://tarnwickfolvendale.com/
https://www.qmvorlu.com/

```html
<!DOCTYPE html>
<html lang="en">
<head>
<meta charset="utf-8">
<title>Brivaloka Optometry – Scleral Contact Lenses</title>
<link href="https://fonts.googleapis.com/css2?family=Montserrat:wght@400;500;600;700&family=Open+Sans:wght@400;600;700&display=swap" rel="stylesheet">
<style>
:root{
  --blue:#1f8fd2;
  --blue-dark:#1a6fa8;
  --yellow:#f6d835;
  --ink:#222a30;
  --text:#7b8287;
  --muted:#a4a9ad;
  --band:#efefef;
  --line:#e3e3e3;
  --white:#ffffff;
  --dark:#1d2226;
}
*{box-sizing:border-box;margin:0;padding:0}
html,body{width:1200px;height:2436px;overflow:hidden;background:var(--white)}
body{position:relative;font-family:"Open Sans",Arial,sans-serif;color:var(--text)}
.abs{position:absolute}

/* header */
.site-header{left:0;top:0;width:1200px;height:100px;background:var(--white)}
.brand{left:32px;top:10px;display:flex;align-items:center;gap:12px}
.brand-square{width:60px;height:60px;background:var(--yellow)}
.brand-name{font-family:"Montserrat",sans-serif;font-weight:600;font-size:15px;color:var(--ink);letter-spacing:.5px}
.top-contact{right:32px;top:14px;display:flex;gap:26px;font-size:12px;color:var(--muted)}
.top-contact span{display:flex;align-items:center;gap:6px}
.main-nav{right:32px;top:56px;display:flex;gap:30px;font-family:"Montserrat",sans-serif;font-size:12px;font-weight:600;color:#555;text-transform:uppercase;align-items:center}
.main-nav .active{color:var(--ink);border-bottom:3px solid var(--yellow);padding-bottom:6px}

/* intro band */
.intro{left:0;top:100px;width:1200px;height:160px;background:var(--band);text-align:center;padding-top:42px}
.page-title{font-family:"Montserrat",sans-serif;font-weight:700;font-size:34px;color:var(--blue);letter-spacing:1px}
.intro-text{width:900px;margin:14px auto 0;font-size:11px;line-height:17px;color:var(--muted)}

/* shared */
.section-title{font-family:"Montserrat",sans-serif;font-weight:700;color:var(--blue);text-transform:uppercase}
.body-copy{font-size:12px;line-height:20px;color:var(--text)}
.body-copy p+p{margin-top:14px}

.types-art{left:28px;top:305px;width:400px;height:380px;background:linear-gradient(180deg,#cfe6f5 0%,#5fa6d8 45%,#c23a3a 80%,#f2b6a8 100%)}
.types-title{left:470px;top:360px;font-size:30px}
.types-copy{left:470px;top:420px;width:690px}

.kera-title{left:70px;top:765px;font-size:24px}
.kera-copy{left:70px;top:815px;width:350px}
.kera-art{left:450px;top:730px;width:720px;height:480px;background:radial-gradient(circle at 55% 50%,#2a6fb0 0%,#5fb0e4 14%,#f3dccd 30%,#f7e8dc 60%,#fbf2ea 100%)}

.dry-title{left:70px;top:1290px;width:460px;font-size:38px;line-height:46px}
.dry-copy{left:590px;top:1290px;width:580px}

/* brands */
.brand-row{left:40px;top:1730px;width:1120px;display:flex;justify-content:space-between;font-family:"Montserrat",sans-serif;font-size:22px;font-weight:600;color:var(--ink);letter-spacing:1px}
.frames-row{left:40px;top:1800px;width:1120px;display:flex;justify-content:space-between}
.frame{width:160px;height:100px;background:linear-gradient(180deg,#f4f1ee,#d9d2cc)}

/* footer */
.site-footer{left:0;top:2000px;width:1200px;height:400px;background:var(--yellow)}
.footer-col{top:40px}
.footer-col h3{font-family:"Montserrat",sans-serif;font-size:18px;font-weight:700;color:var(--ink);margin-bottom:22px}
.footer-col ul{list-style:none;font-size:12px;color:var(--ink)}
.footer-col li{display:flex;align-items:flex-start;gap:10px;margin-bottom:14px;line-height:17px}
.footer-col svg{flex:none;margin-top:1px}
.map-btn{display:inline-block;margin-top:10px;background:var(--dark);color:var(--white);font-size:12px;font-weight:600;padding:12px 22px;border-radius:22px}
.hours li{display:block;margin-bottom:8px}
.hours b{font-weight:700}
.social{display:flex;gap:10px;margin-top:18px}
.social span{width:34px;height:34px;border-radius:50%;background:var(--dark)}
.copyright{left:0;top:2400px;width:1200px;height:36px;background:var(--white);text-align:center;font-size:11px;line-height:36px;color:var(--muted)}
.copyright b{color:var(--ink)}
</style>
</head>
<body>

<header class="site-header abs">
  <div class="brand abs">
    <div class="brand-square"></div>
    <div class="brand-name">Brivaloka Optometry</div>
  </div>
  <div class="top-contact abs">
    <span><svg width="12" height="12" viewBox="0 0 24 24"><path d="M6.6 10.8a15 15 0 0 0 6.6 6.6l2.2-2.2a1 1 0 0 1 1-.25 11 11 0 0 0 3.6.6 1 1 0 0 1 1 1V20a1 1 0 0 1-1 1A17 17 0 0 1 3 4a1 1 0 0 1 1-1h3.5a1 1 0 0 1 1 1 11 11 0 0 0 .6 3.6 1 1 0 0 1-.25 1z" fill="#f6d835"/></svg>(555) 014-2290</span>
    <span><svg width="12" height="12" viewBox="0 0 24 24"><rect x="2" y="5" width="20" height="14" rx="2" fill="#f6d835"/><path d="M2 6l10 7 10-7" stroke="#fff" stroke-width="2" fill="none"/></svg>hello@brivaloka.com</span>
  </div>
  <nav class="main-nav abs">
    <span>Home</span><span>Our Team</span><span class="active">Eye Care</span><span>Myopia Control Clinic</span><span>Eyewear</span><span>Blog</span><span>Contact Us</span>
    <svg width="14" height="14" viewBox="0 0 24 24"><circle cx="10" cy="10" r="7" stroke="#555" stroke-width="2.5" fill="none"/><path d="M15 15l6 6" stroke="#555" stroke-width="2.5"/></svg>
  </nav>
</header>

<section class="intro abs">
  <h1 class="page-title">SCLERAL CONTACT LENSES</h1>
  <div class="intro-text">
    <p>Scleral contact lenses are large-diameter gas permeable lenses designed to vault over the entire cornea and rest on the white of the eye. By creating a smooth optical surface, they correct vision for irregular corneas and protect sensitive eyes.</p>
    <p>Also, the space between the lens and the cornea acts as a fluid reservoir, which keeps the eye hydrated and comfortable all day long.</p>
  </div>
</section>

<div class="types-art abs" role="img" aria-label="Cross-section illustration of an eye wearing a scleral lens, labelled scleral lens, liquid reservoir and sclera"></div>
<h2 class="section-title types-title abs">Types of Scleral</h2>
<div class="body-copy types-copy abs">
  <p>Scleral lenses are classified by their diameter. Corneo-scleral and semi-scleral lenses rest near the junction of the cornea and sclera, while full scleral and mini-scleral lenses are larger and rest entirely on the white of the eye. The larger the lens, the more room it leaves for the fluid reservoir and the more stable it sits during blinking.</p>
  <p>Most common conditions, including advanced keratoconus, post-surgical corneas and severe ocular surface disease, may be managed with these lenses when glasses or soft lenses are not enough. They can be custom made to fit each patient.</p>
</div>

<h2 class="section-title kera-title abs">Scleral for Keratoconus</h2>
<div class="body-copy kera-copy abs">
  <p>Keratoconus thins and bulges the cornea into a cone shape, making vision blurry and distorted. Standard lenses often slide or feel uncomfortable on this irregular surface. A scleral lens vaults over the cone entirely, creating a new smooth front surface for light to focus through. Many patients with keratoconus find that scleral lenses give them sharper, steadier vision and better comfort than any lens they have tried before, often delaying the need for surgery.</p>
</div>
<div class="kera-art abs" role="img" aria-label="Close-up photograph of a blue eye"></div>

<h2 class="section-title dry-title abs">Scleral Contact Lenses for Dry Eyes and Other Eye Problems</h2>
<div class="body-copy dry-copy abs">
  <p>In addition to keratoconus, scleral contact lenses can be used for eyes that have undergone a cornea transplant, and for people with severe dry eyes caused by conditions such as autoimmune disease, graft-versus-host disease and other ocular surface disorders. Advances in lens design allow our doctors to fit lenses that keep the surface bathed in fluid, easing pain and protecting the cornea throughout the day.</p>
</div>

<div class="brand-row abs">
  <span>VEYLA</span><span>ORIN HALE</span><span>MARLOWE &amp; CO.</span><span>STRADON</span><span>CERISE</span><span>KESTREL</span>
</div>
<div class="frames-row abs">
  <div class="frame" role="img" aria-label="Eyeglass frames"></div>
  <div class="frame" role="img" aria-label="Eyeglass frames"></div>
  <div class="frame" role="img" aria-label="Sunglasses"></div>
  <div class="frame" role="img" aria-label="Eyeglass frames"></div>
  <div class="frame" role="img" aria-label="Eyeglass frames"></div>
  <div class="frame" role="img" aria-label="Eyeglass frames"></div>
</div>

<footer class="site-footer abs">
  <div class="footer-col abs" style="left:70px">
    <h3>Brivaloka Optometry</h3>
    <ul>
      <li><svg width="14" height="14" viewBox="0 0 24 24"><path d="M6.6 10.8a15 15 0 0 0 6.6 6.6l2.2-2.2a1 1 0 0 1 1-.25 11 11 0 0 0 3.6.6 1 1 0 0 1 1 1V20a1 1 0 0 1-1 1A17 17 0 0 1 3 4a1 1 0 0 1 1-1h3.5a1 1 0 0 1 1 1 11 11 0 0 0 .6 3.6 1 1 0 0 1-.25 1z" fill="#1d2226"/></svg>(555) 014-2290</li>
      <li><svg width="14" height="14" viewBox="0 0 24 24"><path d="M6.6 10.8a15 15 0 0 0 6.6 6.6l2.2-2.2a1 1 0 0 1 1-.25 11 11 0 0 0 3.6.6 1 1 0 0 1 1 1V20a1 1 0 0 1-1 1A17 17 0 0 1 3 4a1 1 0 0 1 1-1h3.5a1 1 0 0 1 1 1 11 11 0 0 0 .6 3.6 1 1 0 0 1-.25 1z" fill="#1d2226"/></svg>(555) 014-2291</li>
      <li><svg width="14" height="14" viewBox="0 0 24 24"><rect x="2" y="5" width="20" height="14" rx="2" fill="#1d2226"/><path d="M2 6l10 7 10-7" stroke="#f6d835" stroke-width="2" fill="none"/></svg>hello@brivaloka.com</li>
      <li><svg width="14" height="14" viewBox="0 0 24 24"><path d="M12 2a7 7 0 0 0-7 7c0 5 7 13 7 13s7-8 7-13a7 7 0 0 0-7-7z" fill="#1d2226"/><circle cx="12" cy="9" r="2.5" fill="#f6d835"/></svg>4180 Calloway Ave,<br>Veldren, CA 90001</li>
    </ul>
    <span class="map-btn">Get directions on the map</span>
  </div>
  <div class="footer-col abs" style="left:470px">
    <h3>Corvan Hills</h3>
    <ul>
      <li><svg width="14" height="14" viewBox="0 0 24 24"><path d="M6.6 10.8a15 15 0 0 0 6.6 6.6l2.2-2.2a1 1 0 0 1 1-.25 11 11 0 0 0 3.6.6 1 1 0 0 1 1 1V20a1 1 0 0 1-1 1A17 17 0 0 1 3 4a1 1 0 0 1 1-1h3.5a1 1 0 0 1 1 1 11 11 0 0 0 .6 3.6 1 1 0 0 1-.25 1z" fill="#1d2226"/></svg>(555) 018-3340</li>
      <li><svg width="14" height="14" viewBox="0 0 24 24"><rect x="2" y="5" width="20" height="14" rx="2" fill="#1d2226"/><path d="M2 6l10 7 10-7" stroke="#f6d835" stroke-width="2" fill="none"/></svg>corvan@brivaloka.com</li>
      <li><svg width="14" height="14" viewBox="0 0 24 24"><path d="M12 2a7 7 0 0 0-7 7c0 5 7 13 7 13s7-8 7-13a7 7 0 0 0-7-7z" fill="#1d2226"/><circle cx="12" cy="9" r="2.5" fill="#f6d835"/></svg>2265 Larkmont St, Suite 4,<br>Corvan Hills, CA 90002</li>
    </ul>
    <span class="map-btn" style="margin-top:41px">Get directions on the map</span>
  </div>
  <div class="footer-col hours abs" style="left:860px">
    <h3>Opening Hours</h3>
    <ul>
      <li>Monday - Thursday : <b>9 am - 6 pm</b></li>
      <li>Friday : <b>8:30 am - 5 pm</b></li>
      <li>Saturday : <b>8:30 am - 5 pm</b></li>
      <li>Closed on <b>Sunday</b></li>
      <li>Please keep in mind we are closed<br>for <b>lunch 1-2 pm</b></li>
    </ul>
    <div class="social"><span></span><span></span><span></span><span></span></div>
  </div>
</footer>

<div class="copyright abs">Copyright © <b>Brivaloka Optometry</b> - 2019. All rights reserved</div>

</body>
</html>
```